School Communication Email Template

Looking for a designer to create a couple simple email templates that are matching our brand colors and feel. Attached is the default email template that is currently being sent out. Company details can be shared upon request.

Template is to be used within the booking tool we use (snapshot below) and gmail. Template code is in HTML (see screenshot below).
Updates

Template code for website should be in HTML. Sorry if that created confusion.

Target Market(s)

Parents of kids enrolled in our classes

Industry/Entity Type

Kids sport classes

Font styles to use
Serif

Colors
0054AA
0677BA
7BADD7
CADEEF
E8F1F8
FFF300
FFF600
FEFA6F
FFFEC7
FFFEE8

Requirements
Must have
• Consistency with company brand/colors
Nice to have
• Flexibility to be adjusted as needed

```html
<!DOCTYPE html>
<html lang="en">
<head>
<meta charset="utf-8">
<title>Booking Confirmation</title>
<link rel="stylesheet" href="https://fonts.googleapis.com/css2?family=Mulish:wght@400;700;800&family=Roboto:wght@400&display=swap">
<style>
  :root {
    --navy: #263f8a;
    --navy-deep: #22397e;
    --navy-soft: #3a5299;
    --gold: #f8ba27;
    --white: #ffffff;
    --field-text: #555a66;
    --icon: #555555;
  }
  * { margin: 0; padding: 0; box-sizing: border-box; }
  html, body { width: 755px; height: 1200px; overflow: hidden; background: var(--navy); }
  .email {
    position: relative;
    width: 755px;
    height: 1200px;
    overflow: hidden;
    background: var(--navy);
    font-family: "Mulish", sans-serif;
    color: var(--white);
  }
  .backdrop { position: absolute; inset: 0; width: 755px; height: 1200px; }
  .brand-disc {
    position: absolute;
    left: 254px; top: -44px;
    width: 246px; height: 246px;
    border-radius: 50%;
    background: var(--white);
    box-shadow: -20px 6px 0 var(--gold);
    display: flex; align-items: flex-end; justify-content: center;
    padding-bottom: 84px;
  }
  .brand-name {
    font-weight: 800;
    font-size: 24px;
    color: var(--navy);
    letter-spacing: 0.3px;
  }
  .greeting {
    position: absolute; left: 81px; top: 236px;
    font-weight: 700; font-size: 19px;
  }
  .section-tag {
    position: absolute; left: 83px; top: 290px;
    width: 193px; height: 63px;
    background: var(--gold);
    border-radius: 3px;
    display: flex; align-items: center; justify-content: center;
    font-weight: 800; font-size: 32px; letter-spacing: 0.5px;
  }
  .booking-details { position: absolute; left: 0; top: 0; width: 755px; }
  .detail-row {
    position: absolute; left: 0; width: 755px; height: 44px;
    display: flex; align-items: center;
  }
  .detail-label {
    position: absolute; left: 81px;
    font-weight: 700; font-size: 20px;
  }
  .detail-colon {
    position: absolute; left: 259px;
    font-weight: 700; font-size: 19px;
  }
  .detail-field {
    position: absolute; left: 293px;
    width: 398px; height: 44px;
    border-radius: 22px;
    background: var(--white);
    display: flex; align-items: center; justify-content: space-between;
    padding: 0 24px 0 31px;
    font-size: 14.5px; color: var(--field-text);
  }
  .field-icon { width: 14px; height: 14px; }
  .footer-note {
    position: absolute; left: 0; top: 1138px; width: 755px;
    text-align: center;
    font-family: "Roboto", sans-serif;
    font-size: 17px;
  }
</style>
</head>
<body>
<main class="email">
  <svg class="backdrop" viewBox="0 0 800 1272" preserveAspectRatio="none" aria-hidden="true">
    <defs>
      <linearGradient id="skyGlow" x1="0" y1="0" x2="0" y2="1">
        <stop offset="0" stop-color="#31509e"/>
        <stop offset="1" stop-color="#2a4490"/>
      </linearGradient>
      <radialGradient id="mascotGlow" cx="0.5" cy="0.5" r="0.5">
        <stop offset="0" stop-color="#4a5a8e" stop-opacity="0.75"/>
        <stop offset="1" stop-color="#4a5a8e" stop-opacity="0"/>
      </radialGradient>
      <radialGradient id="orbGlow" cx="0.5" cy="0.5" r="0.5">
        <stop offset="0" stop-color="#223a80" stop-opacity="0.8"/>
        <stop offset="1" stop-color="#223a80" stop-opacity="0"/>
      </radialGradient>
    </defs>
    <rect x="0" y="200" width="800" height="610" fill="var(--navy-deep)" opacity="0.4"/>
    <rect class="night-sky" x="0" y="0" width="800" height="200" fill="url(#skyGlow)" role="img" aria-label="Night sky scattered with small gold stars"/>
    <rect class="orb-shapes" x="480" y="120" width="320" height="520" fill="url(#orbGlow)" role="img" aria-label="Faint decorative circles"/>
    <rect class="mascot-shadow" x="-60" y="760" width="540" height="360" fill="url(#mascotGlow)" role="img" aria-label="Faint large star mascot silhouette"/>
    <path class="swoosh-white" d="M14 1240 C240 1060 600 960 800 1082 L800 1115 C600 1010 260 1085 14 1240 Z" fill="var(--white)"/>
    <path class="swoosh-gold" d="M14 1240 C260 1085 600 1010 800 1115 L800 1250 C600 1080 220 1110 14 1240 Z" fill="var(--gold)"/>
  </svg>

  <div class="brand-disc">
    <span class="brand-name">Starlet Sports</span>
  </div>

  <p class="greeting">Dear, Mara Quill</p>
  <div class="section-tag">BOOKING</div>

  <section class="booking-details">
    <div class="detail-row" style="top:387px">
      <span class="detail-label">Student</span><span class="detail-colon">:</span>
      <span class="detail-field">Theo Brandt</span>
    </div>
    <div class="detail-row" style="top:463px">
      <span class="detail-label">Appointment</span><span class="detail-colon">:</span>
      <span class="detail-field">Appointment name</span>
    </div>
    <div class="detail-row" style="top:538px">
      <span class="detail-label">Service</span><span class="detail-colon">:</span>
      <span class="detail-field">Summer Camps</span>
    </div>
    <div class="detail-row" style="top:614px">
      <span class="detail-label">Start Date</span><span class="detail-colon">:</span>
      <span class="detail-field">02-02-2023
        <svg class="field-icon" viewBox="0 0 14 14" aria-hidden="true"><rect x="1.5" y="2.5" width="11" height="10" rx="1" fill="none" stroke="var(--icon)" stroke-width="1.2"/><line x1="1.5" y1="5.5" x2="12.5" y2="5.5" stroke="var(--icon)" stroke-width="1.2"/><line x1="4.5" y1="1" x2="4.5" y2="3.5" stroke="var(--icon)" stroke-width="1.2"/><line x1="9.5" y1="1" x2="9.5" y2="3.5" stroke="var(--icon)" stroke-width="1.2"/></svg>
      </span>
    </div>
    <div class="detail-row" style="top:689px">
      <span class="detail-label">End Date</span><span class="detail-colon">:</span>
      <span class="detail-field">04-02-2023
        <svg class="field-icon" viewBox="0 0 14 14" aria-hidden="true"><rect x="1.5" y="2.5" width="11" height="10" rx="1" fill="none" stroke="var(--icon)" stroke-width="1.2"/><line x1="1.5" y1="5.5" x2="12.5" y2="5.5" stroke="var(--icon)" stroke-width="1.2"/><line x1="4.5" y1="1" x2="4.5" y2="3.5" stroke="var(--icon)" stroke-width="1.2"/><line x1="9.5" y1="1" x2="9.5" y2="3.5" stroke="var(--icon)" stroke-width="1.2"/></svg>
      </span>
    </div>
    <div class="detail-row" style="top:765px">
      <span class="detail-label">Start Time</span><span class="detail-colon">:</span>
      <span class="detail-field">09.00 AM
        <svg class="field-icon" viewBox="0 0 14 14" aria-hidden="true"><circle cx="7" cy="7" r="5.5" fill="none" stroke="var(--icon)" stroke-width="1.3"/><path d="M7 4 V7 H5" fill="none" stroke="var(--icon)" stroke-width="1.3"/></svg>
      </span>
    </div>
    <div class="detail-row" style="top:840px">
      <span class="detail-label">End Time</span><span class="detail-colon">:</span>
      <span class="detail-field">05.00 PM
        <svg class="field-icon" viewBox="0 0 14 14" aria-hidden="true"><circle cx="7" cy="7" r="5.5" fill="none" stroke="var(--icon)" stroke-width="1.3"/><path d="M7 4 V7 H5" fill="none" stroke="var(--icon)" stroke-width="1.3"/></svg>
      </span>
    </div>
  </section>

  <footer class="footer-note">2023 Copyrights&nbsp; | &nbsp;All Rights Reserved</footer>
</main>
</body>
</html>
```